Equipment Finance Specialist I work with companies who need the funds to buy their equipment

I would like a business card that stands out on the shelves. I want to be able to hand it to someone and say WOW. This card should have my logo.
You can put color into it I am very open on design and color

What my company does is we deal with dealerships that sell equipment such as Dump Trucks garbage trucks tractors trailers. Customers get referred to us and depending on their time in business we will ask for the following items

Companies that have been in business for more than two years we have a credit application program up to 250K . With this program we need the following items Credit application filled out(which is what I would like to be able for the customer to click on my website to get.) as well as three current month bank statements.

Deals over 250k we will need the following items

2 years business tax returns
2 years personal tax returns
Profit & Loss statement
Personal Financial Statement

what we do
100% FINANCING
SEASONAL PAYMENTS
LOAN BALLOON PAYMENTS
TRAC LEASING
LOW-INTEREST REFINANCING RATES
DEBT CONSOLIDATION

We specialize in creative financing solutions and offer a variety of reliable, flexible and expandable lending choices.

Target Market(s)

Trucking Companies

Industry/Entity Type

Trucking Company

Contact Information for Business Card

* $250,000 Application only Program
* Loans from $30,000 to 5,000,000
* Competitive Interest Rates

Font styles to use
Serif
Sans Serif

Colors

Designer to choose colors to be used in the design.

Requirements
Must have
• On the back of the card.
• * $250,000 Application only Program
• * Loans from $30,000 to 5,000,000
• My name, email, website. address
• * Competitive Interest Rates
• * 100% Financing
Nice to have
• I want my logo to pop on the card
• My logo is the great one I would like to use
Should not have
• I am up for your creativity as well

```html
<!DOCTYPE html>
<html lang="en">
<head>
<meta charset="utf-8">
<title>Summit Lending – Business Card</title>
<link href="https://fonts.googleapis.com/css2?family=Open+Sans:wght@400;600;700;800&display=swap" rel="stylesheet">
<style>
  :root {
    --navy: #13286e;
    --red: #c8102e;
    --white: #ffffff;
    --ink: #555a63;
    --stage: #2b2b2d;
    --truck-light: #3a4f93;
  }
  * { box-sizing: border-box; margin: 0; padding: 0; }
  html, body { width: 1200px; height: 892px; overflow: hidden; }
  body {
    background: var(--stage);
    font-family: "Open Sans", Arial, sans-serif;
    position: relative;
  }
  .card {
    position: absolute;
    width: 560px;
    height: 320px;
    background: var(--white);
    overflow: hidden;
    box-shadow: 0 10px 24px rgba(0,0,0,.45);
  }

  /* Front */
  .card--front { left: 70px; top: 70px; }
  .brand {
    position: absolute;
    left: 0; right: 0; top: 92px;
    display: flex; align-items: center; justify-content: center; gap: 14px;
  }
  .brand__dot {
    width: 58px; height: 58px; border-radius: 50%;
    background: var(--navy);
  }
  .brand__name {
    font-weight: 800; font-size: 40px; letter-spacing: .5px;
    color: var(--navy); text-transform: uppercase; line-height: 1;
  }
  .offers {
    position: absolute; left: 0; right: 0; top: 210px;
    text-align: center; color: var(--ink);
    font-size: 15px; line-height: 1.35;
  }

  /* Back */
  .card--back { left: 570px; top: 500px; background: var(--navy); }
  .back__art { position: absolute; inset: 0; }
  .back__brand {
    position: absolute; right: 30px; top: 36px;
    font-weight: 800; font-size: 30px; color: var(--white);
    text-transform: uppercase; line-height: 1;
  }
  .back__accent {
    position: absolute; right: 0; top: 94px;
    width: 8px; height: 30px; background: var(--red);
  }
  .contact {
    position: absolute; right: 30px; top: 96px;
    text-align: right; color: var(--white);
    font-size: 13px; line-height: 1.45;
  }
  .contact__name { font-weight: 700; font-size: 17px; letter-spacing: .3px; }
  .contact__title { font-size: 12px; margin-bottom: 14px; letter-spacing: .5px; }
  .contact__label { font-weight: 700; }
</style>
</head>
<body>

  <section class="card card--front">
    <div class="brand">
      <span class="brand__dot"></span>
      <span class="brand__name">Summit Lending</span>
    </div>
    <p class="offers">
      $250,000 Application only Program • Loans from $30,000 to 5,000,000<br>
      Competitive Interest Rates • 100% Financing
    </p>
  </section>

  <section class="card card--back">
    <svg class="back__art" width="560" height="320" viewBox="0 0 560 320">
      <defs>
        <linearGradient id="truckTone" x1="0" y1="0" x2="1" y2="1">
          <stop offset="0" stop-color="#f3f5fb"/>
          <stop offset="1" stop-color="#c9d1e8"/>
        </linearGradient>
      </defs>
      <path d="M0 0 H190 A190 190 0 0 1 190 320 H0 Z" fill="var(--white)"/>
      <path d="M150 330 A175 175 0 0 0 230 10" fill="none" stroke="var(--navy)" stroke-width="18"/>
      <rect x="10" y="40" width="250" height="260" rx="30" fill="url(#truckTone)"
            role="img" aria-label="Illustration of a heavy dump truck, front three-quarter view"/>
    </svg>
    <div class="back__brand">Summit Lending</div>
    <span class="back__accent"></span>
    <div class="contact">
      <p class="contact__name">MARK ELLISON</p>
      <p class="contact__title">PRESIDENT</p>
      <p>2170 Harbor View Road</p>
      <p>Lakeside, NY 10990</p>
      <p><span class="contact__label">P:</span> 555 0142 7788</p>
      <p>mark@summitlending.com</p>
      <p>www.summitlending.com</p>
    </div>
  </section>

</body>
</html>
```